Falkrin homes and renovations business card design.

Would like some new card designs utilizing my new logo that look professional. I am open to different colors on the logo or utilize the same ones we have. I like the original concept but would like to see some fresh ideas and build on what we have already done.

Target Market(s)

Custom home building industry, Real estate sales, Renovation projects.

Industry/Entity Type

Home Builder

Contact Information for Business Card

Falkrin Homes and Renovations
2871 96th Avenue
Frank, Alberta
T2R3W8
Home : 403- 718-4063 Cell: 403- 294-5170

My info is : Dax Falkrin, President and CEO
email: falkrinhomes@maildrop-example.net
Website: falkrinhomes-example.com
websit

Requirements
Must have
• Must Use my new logo design. I am open to different colors on the logo or utilize the same ones in the existing design. I can upload the original logo design if needed.

```html
<!DOCTYPE html>
<html lang="en">
<head>
<meta charset="utf-8">
<title>Falkrin Homes and Renovations – Business Card</title>
<link href="https://fonts.googleapis.com/css2?family=Open+Sans:wght@400;600;700&display=swap" rel="stylesheet">
<style>
  :root {
    --backdrop: #1a1a1a;
    --card: #2a2a2a;
    --card-edge: #333333;
    --gold: #c9962e;
    --gold-soft: #8a6a36;
    --silver: #bdbdbd;
    --text: #e6e6e6;
    --muted: #9a9a9a;
  }
  * { box-sizing: border-box; margin: 0; padding: 0; }
  html, body { width: 1200px; height: 1000px; overflow: hidden; }
  body {
    background: var(--backdrop);
    font-family: "Open Sans", Arial, sans-serif;
    color: var(--text);
    position: relative;
  }
  .card {
    position: absolute;
    left: 220px;
    width: 760px;
    height: 434px;
    background: var(--card);
    border: 1px solid var(--card-edge);
    box-shadow: 0 18px 40px rgba(0,0,0,0.55);
  }
  .card--back { top: 36px; }
  .card--front { top: 530px; }

  /* back side */
  .back-brand {
    position: absolute;
    top: 150px; left: 0; right: 0;
    display: flex; align-items: center; justify-content: center; gap: 14px;
  }
  .brand-mark { width: 18px; height: 18px; }
  .back-brand .brand-mark { background: var(--silver); }
  .back-brand .brand-name {
    font-size: 30px; font-weight: 600; color: var(--silver); letter-spacing: 0.5px;
  }
  .back-web {
    position: absolute;
    bottom: 40px; left: 0; right: 0;
    display: flex; align-items: center; justify-content: center; gap: 10px;
    font-size: 17px; color: var(--text);
  }
  .accent { color: var(--gold); }

  /* front side */
  .front-brand {
    position: absolute;
    left: 50px; top: 138px; width: 280px;
    display: flex; align-items: flex-start; gap: 12px;
  }
  .front-brand .brand-mark { background: var(--gold); margin-top: 8px; flex: none; }
  .front-brand .brand-name {
    font-size: 27px; font-weight: 600; color: var(--gold); line-height: 1.25;
  }
  .divider {
    position: absolute;
    left: 345px; top: 110px;
    width: 2px; height: 145px;
    background: var(--muted);
  }
  .person {
    position: absolute;
    left: 372px; top: 98px;
  }
  .person-name {
    font-size: 28px; font-weight: 600; color: var(--gold-soft); letter-spacing: 1.5px;
  }
  .person-title {
    font-size: 17px; font-weight: 700; color: #ffffff; margin-top: 0;
  }
  .contact-list {
    position: absolute;
    left: 372px; top: 186px;
    list-style: none;
  }
  .contact-list li {
    display: flex; align-items: center; gap: 14px;
    font-size: 17.5px; line-height: 25px; color: var(--text);
  }
  .icon { width: 15px; height: 15px; flex: none; }
  .address {
    position: absolute;
    left: 250px; bottom: 70px;
    display: flex; align-items: center; gap: 16px;
    font-size: 18px; color: var(--text); letter-spacing: 0.5px;
  }
</style>
</head>
<body>

<section class="card card--back" aria-label="Card back">
  <div class="back-brand">
    <span class="brand-mark"></span>
    <span class="brand-name">Falkrin Homes and Renovations</span>
  </div>
  <div class="back-web">
    <svg class="icon" viewBox="0 0 16 16" aria-hidden="true">
      <circle cx="8" cy="8" r="7" fill="var(--gold)"/>
      <path d="M1 8h14M8 1c-3 3.5-3 10.5 0 14M8 1c3 3.5 3 10.5 0 14" stroke="var(--card)" stroke-width="1" fill="none"/>
    </svg>
    <span>www.<span class="accent">falkrinhomes-example</span>.com</span>
  </div>
</section>

<section class="card card--front" aria-label="Card front">
  <div class="front-brand">
    <span class="brand-mark"></span>
    <span class="brand-name">Falkrin Homes and Renovations</span>
  </div>

  <div class="divider"></div>

  <div class="person">
    <p class="person-name">Dax Falkrin</p>
    <p class="person-title">President and CEO</p>
  </div>

  <ul class="contact-list">
    <li>
      <svg class="icon" viewBox="0 0 16 16" aria-hidden="true">
        <path d="M3 1.5l3 3-1.6 1.8c.9 2 2.4 3.5 4.3 4.3L10.5 9l3 3-1.8 2.3C6.5 14 2 9.5 1.7 3.3z" fill="var(--gold)"/>
      </svg>
      <span>403 718 4063</span>
    </li>
    <li>
      <svg class="icon" viewBox="0 0 16 16" aria-hidden="true">
        <rect x="4" y="1" width="8" height="14" rx="1.5" fill="none" stroke="var(--gold)" stroke-width="1.6"/>
      </svg>
      <span>403 294 5170</span>
    </li>
    <li>
      <svg class="icon" viewBox="0 0 16 16" aria-hidden="true">
        <rect x="1" y="3" width="14" height="10" fill="var(--gold)"/>
        <path d="M1 3l7 6 7-6" stroke="var(--card)" stroke-width="1.2" fill="none"/>
      </svg>
      <span>falkrinhomes@maildrop-example.net</span>
    </li>
    <li>
      <svg class="icon" viewBox="0 0 16 16" aria-hidden="true">
        <circle cx="9.5" cy="6.5" r="4.5" fill="none" stroke="var(--gold)" stroke-width="1.8"/>
        <path d="M6.2 9.8L1.5 14.5" stroke="var(--gold)" stroke-width="2.2"/>
      </svg>
      <span>www.<span class="accent">falkrinhomes-example</span>.com</span>
    </li>
  </ul>

  <div class="address">
    <svg class="icon" viewBox="0 0 16 16" aria-hidden="true">
      <path d="M8 15.5S2.5 9.5 2.5 6a5.5 5.5 0 0 1 11 0c0 3.5-5.5 9.5-5.5 9.5z" fill="var(--gold)"/>
      <circle cx="8" cy="6" r="2" fill="var(--card)"/>
    </svg>
    <span>2871 96th Avenue Frank, Alberta</span>
  </div>
</section>

</body>
</html>
```